Dental Medical History Form - Content provided

Design a medical history form for a dental practice. Content is provided so all that is needed is the formatting to make it look great and easy to read.

"Patient Information" to include all information contained in top portion of the "Patient Medical History Form" docx file.

"Medical History" should follow the formatting and content of the "Exact Medical History" file as this is what the entry fields look like in our practice software and so we would like it to match.

1st page - Patient info, allergies, medications, antibiotics, joint replacement, pregnancy.

2nd page - Do you have, or have you had, any of the following? . . . . . . .
Updates

Target Market(s)

All ages but must be clear enough for elderly to read. Use as much space as possible to keep font size bigger yet keep to two pages

Industry/Entity Type

Dental

Font styles to use
Sans Serif

Requirements
Must have
• All content provided
• Our logo at the top (file provided)
• Century Gothic Font
• Limit to two pages

```html
<!DOCTYPE html>
<html lang="en">
<head>
<meta charset="UTF-8">
<title>Medical History Form – Page 2</title>
<link href="https://fonts.googleapis.com/css2?family=Fira+Sans+Condensed:wght@400;700&display=swap" rel="stylesheet">
<style>
  :root {
    --bg: #e6e6e6;
    --paper: #ffffff;
    --navy: #2b3553;
    --ink: #3a4260;
    --band-dark: #a9abb2;
    --band-light: #f4f4f5;
    --box: #3a4260;
  }
  * { box-sizing: border-box; margin: 0; padding: 0; }
  html, body {
    width: 1200px; height: 784px; overflow: hidden;
    background: var(--bg);
    font-family: "Fira Sans Condensed", "Arial Narrow", sans-serif;
    color: var(--ink);
  }
  .form-page {
    position: absolute; left: 320px; top: 12px;
    width: 560px; height: 760px;
    background: var(--paper);
    box-shadow: 0 2px 6px rgba(0,0,0,.12);
    padding: 0 0 14px;
  }
  .question-band {
    height: 30px;
    background: linear-gradient(to bottom, var(--band-dark), var(--band-light));
    border-top: 3px solid var(--navy);
    display: flex; align-items: center; justify-content: center;
    font-weight: 700; font-size: 13px; color: var(--navy);
  }
  .columns {
    display: grid; grid-template-columns: 1fr 1fr; column-gap: 34px;
    padding: 8px 34px 0;
  }
  .master-row { justify-content: flex-end; margin-bottom: 2px; }
  .row {
    display: flex; align-items: center;
    height: 14.6px; font-size: 9.5px; line-height: 1;
  }
  .row .label { flex: 1; white-space: nowrap; }
  .section-title { font-weight: 700; color: var(--navy); }
  .answer { display: flex; align-items: center; gap: 3px; margin-left: 6px; }
  .answer .box {
    width: 9px; height: 9px; border: 1px solid var(--box); display: inline-block;
    margin-right: 5px;
  }
  .other-conditions { margin-top: 10px; }
  .other-conditions h3 { font-size: 10.5px; font-weight: 700; color: var(--navy); margin-bottom: 4px; }
  .write-line { height: 16px; border: 1px solid var(--ink); border-bottom: none; }
  .write-line:last-child { border-bottom: 1px solid var(--ink); }
  .sign-row {
    position: absolute; left: 34px; right: 34px; bottom: 42px;
    display: grid; grid-template-columns: 1fr 1fr; column-gap: 34px;
  }
  .sign-field { display: flex; align-items: flex-end; gap: 8px; font-weight: 700; font-size: 10.5px; color: var(--navy); }
  .sign-field .line { flex: 1; border-bottom: 1px solid var(--ink); height: 12px; }
  .closing-note {
    position: absolute; left: 34px; right: 34px; bottom: 14px;
    text-align: center; font-size: 7px; line-height: 1.35; color: var(--ink);
  }
</style>
</head>
<body>
<main class="form-page">
  <header class="question-band">Do you have, or have you had, any of the following?</header>

  <section class="columns">
    <div class="column">
      <div class="row section-title"><span class="label">Dental</span></div>
      <div class="row"><span class="label">Acid Reflux</span><span class="answer">Yes <span class="box"></span>No <span class="box"></span></span></div>
      <div class="row"><span class="label">Bad Breath/Taste</span><span class="answer">Yes <span class="box"></span>No <span class="box"></span></span></div>
      <div class="row"><span class="label">Bleeding/Swollen/Sore Gums</span><span class="answer">Yes <span class="box"></span>No <span class="box"></span></span></div>
      <div class="row"><span class="label">Blisters/Ulcers in Mouth</span><span class="answer">Yes <span class="box"></span>No <span class="box"></span></span></div>
      <div class="row"><span class="label">Broken tooth/filling</span><span class="answer">Yes <span class="box"></span>No <span class="box"></span></span></div>
      <div class="row"><span class="label">Burning tongue</span><span class="answer">Yes <span class="box"></span>No <span class="box"></span></span></div>
      <div class="row"><span class="label">Dry mouth</span><span class="answer">Yes <span class="box"></span>No <span class="box"></span></span></div>
      <div class="row"><span class="label">Food collection between teeth</span><span class="answer">Yes <span class="box"></span>No <span class="box"></span></span></div>
      <div class="row"><span class="label">Grinding/clenching teeth (day/night)</span><span class="answer">Yes <span class="box"></span>No <span class="box"></span></span></div>
      <div class="row"><span class="label">Loose teeth</span><span class="answer">Yes <span class="box"></span>No <span class="box"></span></span></div>
      <div class="row"><span class="label">Crooked teeth</span><span class="answer">Yes <span class="box"></span>No <span class="box"></span></span></div>
      <div class="row"><span class="label">Discoloured teeth</span><span class="answer">Yes <span class="box"></span>No <span class="box"></span></span></div>
      <div class="row"><span class="label">Sensitivity to Hot/Cold</span><span class="answer">Yes <span class="box"></span>No <span class="box"></span></span></div>
      <div class="row"><span class="label">Tooth pain when chewing</span><span class="answer">Yes <span class="box"></span>No <span class="box"></span></span></div>
      <div class="row"><span class="label">Jaw pain/Fracture</span><span class="answer">Yes <span class="box"></span>No <span class="box"></span></span></div>
      <div class="row"><span class="label">Orthodontic treatment/history</span><span class="answer">Yes <span class="box"></span>No <span class="box"></span></span></div>
      <div class="row"><span class="label">Oral Cancer</span><span class="answer">Yes <span class="box"></span>No <span class="box"></span></span></div>
      <div class="row section-title"><span class="label">Diet/Lifestyle</span></div>
      <div class="row"><span class="label">Drink more than one glass alcohol per day</span><span class="answer">Yes <span class="box"></span>No <span class="box"></span></span></div>
      <div class="row"><span class="label">Smoking</span><span class="answer">Yes <span class="box"></span>No <span class="box"></span></span></div>
      <div class="row"><span class="label">Carbonated drinks</span><span class="answer">Yes <span class="box"></span>No <span class="box"></span></span></div>
      <div class="row"><span class="label">Sugary foods</span><span class="answer">Yes <span class="box"></span>No <span class="box"></span></span></div>
      <div class="row section-title"><span class="label">Blood</span></div>
      <div class="row"><span class="label">Anaemia</span><span class="answer">Yes <span class="box"></span>No <span class="box"></span></span></div>
      <div class="row"><span class="label">Blood Clots</span><span class="answer">Yes <span class="box"></span>No <span class="box"></span></span></div>
      <div class="row"><span class="label">Leukemia</span><span class="answer">Yes <span class="box"></span>No <span class="box"></span></span></div>
      <div class="row"><span class="label">Low platelets</span><span class="answer">Yes <span class="box"></span>No <span class="box"></span></span></div>
      <div class="row section-title"><span class="label">Chest</span></div>
      <div class="row"><span class="label">Bronchitis</span><span class="answer">Yes <span class="box"></span>No <span class="box"></span></span></div>
      <div class="row"><span class="label">Emphysema</span><span class="answer">Yes <span class="box"></span>No <span class="box"></span></span></div>
      <div class="row"><span class="label">Pneumonia</span><span class="answer">Yes <span class="box"></span>No <span class="box"></span></span></div>
      <div class="row section-title"><span class="label">Infectious Disease</span></div>
      <div class="row"><span class="label">Hepatitis A,B,C,D</span><span class="answer">Yes <span class="box"></span>No <span class="box"></span></span></div>
      <div class="row"><span class="label">HIV/AIDS</span><span class="answer">Yes <span class="box"></span>No <span class="box"></span></span></div>
      <div class="row"><span class="label">Shingles</span><span class="answer">Yes <span class="box"></span>No <span class="box"></span></span></div>
      <div class="row"><span class="label">Tuberculosis</span><span class="answer">Yes <span class="box"></span>No <span class="box"></span></span></div>
    </div>

    <div class="column">
      <div class="row master-row"><span class="answer">Yes <span class="box"></span>No <span class="box"></span></span></div>
      <div class="row section-title"><span class="label">Heart</span></div>
      <div class="row"><span class="label">Liver/Kidney Disease</span><span class="answer">Yes <span class="box"></span>No <span class="box"></span></span></div>
      <div class="row"><span class="label">Angina</span><span class="answer">Yes <span class="box"></span>No <span class="box"></span></span></div>
      <div class="row"><span class="label">Atrial Fibrillation</span><span class="answer">Yes <span class="box"></span>No <span class="box"></span></span></div>
      <div class="row"><span class="label">Blood Pressure (High/Low)</span><span class="answer">Yes <span class="box"></span>No <span class="box"></span></span></div>
      <div class="row"><span class="label">Congenital Heart Disease</span><span class="answer">Yes <span class="box"></span>No <span class="box"></span></span></div>
      <div class="row"><span class="label">Heart attack</span><span class="answer">Yes <span class="box"></span>No <span class="box"></span></span></div>
      <div class="row"><span class="label">Heart murmur</span><span class="answer">Yes <span class="box"></span>No <span class="box"></span></span></div>
      <div class="row"><span class="label">Heart surgery</span><span class="answer">Yes <span class="box"></span>No <span class="box"></span></span></div>
      <div class="row"><span class="label">Heart valve replacement</span><span class="answer">Yes <span class="box"></span>No <span class="box"></span></span></div>
      <div class="row"><span class="label">Infective endocarditis</span><span class="answer">Yes <span class="box"></span>No <span class="box"></span></span></div>
      <div class="row"><span class="label">Rheumatic Heart Disease</span><span class="answer">Yes <span class="box"></span>No <span class="box"></span></span></div>
      <div class="row"><span class="label">Pacemaker</span><span class="answer">Yes <span class="box"></span>No <span class="box"></span></span></div>
      <div class="row"><span class="label">Stent</span><span class="answer">Yes <span class="box"></span>No <span class="box"></span></span></div>
      <div class="row section-title"><span class="label">Other</span></div>
      <div class="row"><span class="label">Anxiety/PTSD</span><span class="answer">Yes <span class="box"></span>No <span class="box"></span></span></div>
      <div class="row"><span class="label">Arthritis</span><span class="answer">Yes <span class="box"></span>No <span class="box"></span></span></div>
      <div class="row"><span class="label">Alzheimer's</span><span class="answer">Yes <span class="box"></span>No <span class="box"></span></span></div>
      <div class="row"><span class="label">Asthma</span><span class="answer">Yes <span class="box"></span>No <span class="box"></span></span></div>
      <div class="row"><span class="label">Anaphylaxis</span><span class="answer">Yes <span class="box"></span>No <span class="box"></span></span></div>
      <div class="row"><span class="label">Auto-immune disease/Depression</span><span class="answer">Yes <span class="box"></span>No <span class="box"></span></span></div>
      <div class="row"><span class="label">Diabetes</span><span class="answer">Yes <span class="box"></span>No <span class="box"></span></span></div>
      <div class="row"><span class="label">Epilepsy</span><span class="answer">Yes <span class="box"></span>No <span class="box"></span></span></div>
      <div class="row"><span class="label">Kidney Disease</span><span class="answer">Yes <span class="box"></span>No <span class="box"></span></span></div>
      <div class="row"><span class="label">Liver Disease</span><span class="answer">Yes <span class="box"></span>No <span class="box"></span></span></div>
      <div class="row"><span class="label">Osteoporosis</span><span class="answer">Yes <span class="box"></span>No <span class="box"></span></span></div>
      <div class="row"><span class="label">Radiation to Head/Neck</span><span class="answer">Yes <span class="box"></span>No <span class="box"></span></span></div>
      <div class="row"><span class="label">Snoring</span><span class="answer">Yes <span class="box"></span>No <span class="box"></span></span></div>
      <div class="row"><span class="label">Sleep apnea</span><span class="answer">Yes <span class="box"></span>No <span class="box"></span></span></div>
      <div class="row"><span class="label">Stroke</span><span class="answer">Yes <span class="box"></span>No <span class="box"></span></span></div>

      <div class="other-conditions">
        <h3>Please list any other conditions we should be aware of:</h3>
        <div class="write-line"></div>
        <div class="write-line"></div>
        <div class="write-line"></div>
        <div class="write-line"></div>
        <div class="write-line"></div>
        <div class="write-line"></div>
        <div class="write-line"></div>
      </div>
    </div>
  </section>

  <div class="sign-row">
    <div class="sign-field">Signature <span class="line"></span></div>
    <div class="sign-field">Date <span class="line"></span></div>
  </div>

  <p class="closing-note">Thank you for the time to complete your medical history form.<br>
  Oral health is linked to overall health and this comprehensive questionnaire will help us to provide you with optimal and safe care.</p>
</main>
</body>
</html>
```